Business Card Design Project

Actor, Producer, Vocal Coach, Choral Director, Song WriterPhone: (215) 555-0142 Fax: (215) 856-3933Email: waltierblocker@gmail.comFacebook: facebook.com/waltier.blockerTwitter: @thedf482

Industry/Entity Type

Business

Contact Information for Business Card

Business Cards that include my picture

Colors

Designer to choose colors to be used in the design.

```html
<!DOCTYPE html>
<html lang="en">
<head>
<meta charset="utf-8">
<title>Dorian Fellsmore – Business Card</title>
<link rel="stylesheet" href="https://fonts.googleapis.com/css2?family=Mulish:wght@300;400;500&display=swap">
<style>
  :root {
    --backdrop: #d8d3ce;
    --card-black: #0b0b0c;
    --card-sheen: #1c1c1e;
    --accent-pink: #e8679f;
    --text-white: #f4f4f4;
    --photo-light: #f2f2f2;
    --photo-mid: #cfcfd2;
  }
  * { box-sizing: border-box; margin: 0; padding: 0; }
  html, body {
    width: 1200px; height: 1023px; overflow: hidden;
    background: var(--backdrop);
    font-family: "Mulish", sans-serif;
  }
  .business-card {
    position: absolute; left: 100px; top: 226px;
    width: 1000px; height: 571px;
    border-radius: 34px;
    background: linear-gradient(135deg, var(--card-sheen) 0%, var(--card-black) 55%);
    box-shadow: 0 18px 40px rgba(0,0,0,.35);
    overflow: hidden;
  }
  .portrait-frame {
    position: absolute; left: 92px; top: 148px;
    width: 270px; height: 330px;
    border: 2px solid var(--accent-pink);
    padding: 8px;
  }
  .portrait-photo {
    width: 100%; height: 100%;
    background: linear-gradient(160deg, var(--photo-light) 0%, var(--photo-mid) 70%, #b9a9b2 100%);
  }
  .identity {
    position: absolute; left: 440px; top: 150px; width: 520px;
  }
  .identity-name {
    color: var(--accent-pink);
    font-size: 46px; font-weight: 500; letter-spacing: 1px; line-height: 1.05;
  }
  .identity-roles {
    margin-top: 10px;
    color: var(--text-white);
    font-size: 21px; font-weight: 300; line-height: 1.35; letter-spacing: .3px;
  }
  .contact-list {
    list-style: none; margin-top: 30px;
  }
  .contact-item {
    display: flex; align-items: center; gap: 16px;
    color: var(--text-white);
    font-size: 20px; font-weight: 300; line-height: 1.6; letter-spacing: .3px;
  }
  .contact-icon { width: 16px; height: 16px; flex: none; }
</style>
</head>
<body>
  <div class="business-card">
    <div class="portrait-frame">
      <div class="portrait-photo" role="img" aria-label="Portrait photo of the performer in a white shirt and pink tie"></div>
    </div>

    <div class="identity">
      <h1 class="identity-name">Dorian Fellsmore</h1>
      <p class="identity-roles">Actor, Producer, Vocal Coach,<br>Choral Director, Song Writer</p>

      <ul class="contact-list">
        <li class="contact-item">
          <svg class="contact-icon" viewBox="0 0 16 16" aria-hidden="true"><path d="M4 1.5 6.2 4.2 4.8 5.9c.9 2 2.4 3.5 4.3 4.3l1.7-1.4 2.7 2.2-1.3 2.3C6.8 13.4 2.6 9.2 1.8 3.8Z" fill="var(--accent-pink)"/></svg>
          <span>(215) 555-0142</span>
        </li>
        <li class="contact-item">
          <svg class="contact-icon" viewBox="0 0 16 16" aria-hidden="true"><rect x="1.5" y="6" width="13" height="8" rx="1.5" fill="var(--accent-pink)"/><rect x="4.5" y="2" width="7" height="4.5" fill="none" stroke="var(--accent-pink)" stroke-width="1.4"/></svg>
          <span>(215) 555-0187</span>
        </li>
        <li class="contact-item">
          <svg class="contact-icon" viewBox="0 0 16 16" aria-hidden="true"><rect x="1.5" y="3.5" width="13" height="9" fill="none" stroke="var(--accent-pink)" stroke-width="1.4"/><path d="M1.8 4 8 9l6.2-5" fill="none" stroke="var(--accent-pink)" stroke-width="1.4"/></svg>
          <span>dorianfellsmore@postlane.net</span>
        </li>
        <li class="contact-item">
          <svg class="contact-icon" viewBox="0 0 16 16" aria-hidden="true"><circle cx="8" cy="8" r="5" fill="var(--accent-pink)"/></svg>
          <span>socialpage.net/dorian.fellsmore</span>
        </li>
        <li class="contact-item">
          <svg class="contact-icon" viewBox="0 0 16 16" aria-hidden="true"><circle cx="8" cy="8" r="5" fill="var(--accent-pink)"/></svg>
          <span>@thedf482</span>
        </li>
      </ul>
    </div>
  </div>
</body>
</html>
```